Design a Travel and Tourism website

We would like a freelancer to design a website that is essentially easy to use and navigate database providing local information for Travelers about destination countries.

We proposed website would discuss different rates, fees, visa requirement, resort locations, cheap flights, etc. This website should be elegant and modern. Our business name is rovanix.
Some reference websites are zemplorift.ca, brindlefoxhaven.com,
There should be a forum in the website where travell\ers discuss about their first hand tranvel experience to such destinations.

Tourism

```html
<!DOCTYPE html>
<html lang="en">
<head>
<meta charset="utf-8">
<title>Rovanix – Travel &amp; Tourism</title>
<link href="https://fonts.googleapis.com/css2?family=Montserrat:wght@400;500;600;700&family=Merienda:wght@400;700&family=Roboto:wght@400;500;700&display=swap" rel="stylesheet">
<style>
:root{
  --teal:#10a197;
  --teal-dark:#0b857d;
  --gold:#b99a57;
  --gold-light:#d8c59a;
  --ink:#2e2b2c;
  --text:#444;
  --muted:#777;
  --line:#e3dccb;
  --grey-bg:#efefef;
  --white:#fff;
}
*{box-sizing:border-box;margin:0;padding:0}
html,body{width:1200px;height:2564px;overflow:hidden;background:var(--white)}
body{position:relative;font-family:"Roboto",sans-serif;color:var(--text)}
.abs{position:absolute}
.heading{font-family:"Montserrat",sans-serif;font-weight:700;color:var(--ink);text-align:center;letter-spacing:.5px}

/* top bar + nav */
.topbar{left:0;top:0;width:1200px;height:19px;background:#2a2626;z-index:2}
.topbar a{position:absolute;top:0;font:500 9px/19px "Roboto",sans-serif;color:var(--gold);text-decoration:none;letter-spacing:.4px}
.mainnav{left:0;top:19px;width:1200px;height:44px;background:var(--teal);z-index:2}
.mainnav a{position:absolute;top:0;height:44px;font:700 12px/44px "Roboto",sans-serif;color:var(--white);text-decoration:none;letter-spacing:.6px}
.mainnav a.active{background:var(--gold);padding:0 18px}
.brand-badge{left:516px;top:0;width:168px;height:82px;background:var(--white);border-radius:0 0 28px 28px;box-shadow:0 2px 6px rgba(0,0,0,.25);display:flex;align-items:center;justify-content:center;z-index:5}
.brand-name{font:700 28px/1 "Merienda",cursive;color:var(--ink)}

/* hero */
.hero{left:0;top:63px;width:1200px;height:556px;background:linear-gradient(180deg,#5e4a6e 0%,#a0738a 22%,#b68472 34%,#5a3e5a 55%,#2b1f33 100%)}
.hero-title{left:140px;top:262px;font:700 44px/1.08 "Montserrat",sans-serif;color:var(--white);letter-spacing:.5px}
.offer-badge{left:866px;top:166px;width:188px;height:188px;border-radius:50%;background:#2c2530;border:4px solid #3f3540;box-shadow:0 0 0 3px var(--gold);overflow:hidden;text-align:center;color:var(--white)}
.offer-badge .city{margin-top:48px;font:700 24px/1.2 "Merienda",cursive}
.offer-badge .price{font:400 11px/1.4 "Roboto",sans-serif;margin-top:4px}
.offer-badge .price b{font:700 17px "Roboto",sans-serif;color:var(--gold-light)}
.offer-badge .foot{position:absolute;left:0;bottom:0;width:100%;height:66px;background:var(--gold-light);display:flex;align-items:center;justify-content:center;font:700 14px/1 "Merienda",cursive;color:var(--teal)}
.offer-badge .star{position:absolute;left:78px;top:12px}
.hero-dots{left:1184px;top:214px}
.hero-dots i{display:block;width:5px;height:5px;border-radius:50%;background:rgba(255,255,255,.7);margin-bottom:8px}

.search{left:0;top:410px;width:1200px;height:209px;background:rgba(25,18,38,.72)}
.tabs{position:absolute;left:301px;top:34px;display:flex;gap:8px}
.tabs span{height:28px;padding:0 12px;background:#4a4550;color:var(--white);font:700 13px/28px "Merienda",cursive}
.tabs span.active{background:var(--gold)}
.field{position:absolute;top:77px}
.field label{display:block;font:700 8px/1.2 "Roboto",sans-serif;color:var(--white);letter-spacing:.3px;margin-bottom:3px}
.field .box{height:37px;background:var(--white);display:flex;align-items:center;padding:0 8px;font:400 10px "Roboto",sans-serif;color:#aaa;gap:6px}
.field .select{justify-content:space-between;color:#333;font-size:14px}
.addcar{left:456px;top:150px;font:700 13px/1 "Merienda",cursive;color:var(--white);display:flex;align-items:center;gap:6px}
.addcar i{width:9px;height:9px;background:var(--gold-light)}
.btn{display:flex;align-items:center;justify-content:center;background:var(--teal);color:var(--white);font:700 14px/1 "Merienda",cursive}
.search .btn{position:absolute;left:552px;top:140px;width:96px;height:38px}

/* favourites */
.fav-title{left:0;top:668px;width:1200px;font-size:25px;line-height:30px}
.fav-tabs{left:142px;top:709px;width:916px;height:29px;border-bottom:1px solid var(--line)}
.fav-tabs span{position:absolute;top:0;height:29px;font:400 13px/29px "Merienda",cursive;color:var(--gold)}
.fav-tabs span.active{background:var(--gold);color:var(--white);padding:0 20px}
.card{position:absolute;top:778px;width:222px;height:194px;overflow:hidden}
.card .label{position:absolute;left:8px;bottom:8px;font:700 13px/1.2 "Merienda",cursive;color:var(--white)}
.card .corner{position:absolute;right:0;bottom:0}
.card .center{position:absolute;left:0;top:66px;width:100%;text-align:center;color:var(--white)}
.card .center .t{font:400 25px/1.2 "Merienda",cursive}
.card .center .p{font:400 12px/1.3 "Roboto",sans-serif;margin-top:4px}
.card .center .p b{font-size:18px}
.fav-dots{left:578px;top:994px;display:flex;gap:9px}
.fav-dots i{width:5px;height:5px;border-radius:50%;background:#ccc}
.fav-dots i.on{background:var(--gold)}

/* forum */
.forum{left:0;top:1051px;width:1200px;height:610px;background:var(--grey-bg)}
.forum-title{left:0;top:1104px;width:1200px;font-size:25px;line-height:30px}
.forum-sub{left:0;top:1134px;width:1200px;text-align:center;font:400 13px/1.3 "Merienda",cursive;color:var(--gold)}
.forum-table{left:142px;top:1183px;width:916px;background:var(--white);border:1px solid var(--line);border-collapse:collapse}
.forum-table th{height:36px;background:var(--gold);color:var(--white);font:700 10px "Roboto",sans-serif;text-align:left;letter-spacing:.3px}
.forum-table td{height:66px;border-bottom:1px solid #ececec;vertical-align:top;padding-top:20px;font:400 10px/1.3 "Roboto",sans-serif;color:#555}
.forum-table tr:last-child td{border-bottom:none;height:74px}
.forum-table .c1{padding-left:24px;width:513px}
.forum-table .c3{text-align:right;padding-right:20px}
.topic{font:600 13px/1.3 "Montserrat",sans-serif;color:var(--gold);margin-bottom:4px}
.stat b{font-weight:400;color:var(--gold)}
.forum .btn{position:absolute;left:552px;top:526px;width:96px;height:31px}

/* newsletter */
.newsletter{left:0;top:1661px;width:1200px;height:173px;background:linear-gradient(90deg,#0f9d93,#14ab9f 50%,#0e8f86)}
.nl-title{left:0;top:45px;width:1200px;text-align:center;font:700 18px/1.2 "Montserrat",sans-serif;color:var(--white);letter-spacing:.5px}
.nl-sub{left:0;top:68px;width:1200px;text-align:center;font:400 12px/1.3 "Merienda",cursive;color:var(--white)}
.nl-input{left:381px;top:92px;width:342px;height:38px;background:var(--white);display:flex;align-items:center;gap:8px;padding-left:14px;font:400 10px "Roboto",sans-serif;color:#999}
.nl-submit{left:728px;top:92px;width:91px;height:38px;background:var(--gold)}

/* links */
.links-title{left:0;top:1889px;width:1200px;font-size:25px;line-height:30px}
.plink{position:absolute;width:289px;height:51px;display:flex;align-items:center;padding-left:44px;font:400 14px/1 "Merienda",cursive;color:var(--ink)}
.plink svg.shape{position:absolute;left:0;top:0}
.plink svg.tick{position:absolute;left:18px;top:20px}
.plink span{position:relative}

/* footer */
.foot-brand{left:0;top:2310px;width:1200px;text-align:center;font:700 28px/1.2 "Merienda",cursive;color:var(--ink)}
.foot-nav{left:0;top:2380px;width:1200px;display:flex;justify-content:center;gap:26px}
.foot-nav a{font:700 10px/1.2 "Roboto",sans-serif;color:var(--ink);text-decoration:none;letter-spacing:.5px}
.copy{left:0;top:2402px;width:1200px;text-align:center;font:400 10px/1.2 "Roboto",sans-serif;color:#555;letter-spacing:.6px}
.skyline{left:0;top:2440px;width:1200px;height:124px;background:linear-gradient(180deg,rgba(185,154,87,0) 0%,#c9ad75 45%,#a98a48 100%)}
</style>
</head>
<body>

<header>
  <div class="abs topbar">
    <a style="left:878px">ACCOUNT ▾</a>
    <a style="left:947px">MY TRIPS</a>
    <a style="left:1009px">SUPPORT ▾</a>
  </div>
  <nav class="abs mainnav">
    <a class="active" style="left:142px">HOME</a>
    <a style="left:238px">HOLIDAYS</a>
    <a style="left:339px">FLIGHTS</a>
    <a style="left:431px">HOTELS</a>
    <a style="left:727px">CARS</a>
    <a style="left:801px">DEALS</a>
    <a style="left:880px">INSURANCE</a>
    <a style="left:991px">FORUM</a>
  </nav>
  <div class="abs brand-badge"><span class="brand-name">Rovanix</span></div>
</header>

<section class="abs hero" role="img" aria-label="City skyline at dusk with a domed historic building"></section>
<h1 class="abs hero-title">START YOUR DREAM<br>HOLIDAYS RIGHT HERE</h1>
<div class="abs offer-badge">
  <svg class="star" width="24" height="24" viewBox="0 0 24 24"><path d="M12 3l2.6 6 6.4.5-4.9 4.2 1.5 6.3L12 16.6 6.4 20l1.5-6.3L3 9.5 9.4 9z" fill="var(--gold)"/></svg>
  <div class="city">Berlin</div>
  <div class="price">From <b>$500</b> per person</div>
  <div class="foot">Rovanix</div>
</div>
<div class="abs hero-dots"><i></i><i></i><i></i><i></i></div>

<section class="abs search">
  <div class="tabs">
    <span class="active">Flight &amp; Hotel</span><span>Holidays</span><span>Flights</span><span>Hotels</span><span>Cars</span><span>Insurance</span><span>Extras</span>
  </div>
  <div class="field" style="left:142px;width:226px"><label>FLYING FROM</label><div class="box"><svg width="9" height="12" viewBox="0 0 9 12"><path d="M4.5 0A4.5 4.5 0 0 0 0 4.5C0 8 4.5 12 4.5 12S9 8 9 4.5A4.5 4.5 0 0 0 4.5 0z" fill="#bbb"/></svg>City or Airport</div></div>
  <div class="field" style="left:373px;width:225px"><label>FLYING TO</label><div class="box"><svg width="9" height="12" viewBox="0 0 9 12"><path d="M4.5 0A4.5 4.5 0 0 0 0 4.5C0 8 4.5 12 4.5 12S9 8 9 4.5A4.5 4.5 0 0 0 4.5 0z" fill="#bbb"/></svg>City or Airport</div></div>
  <div class="field" style="left:603px;width:120px"><label>DEPARTING</label><div class="box"><svg width="11" height="11" viewBox="0 0 11 11"><rect x=".5" y="1.5" width="10" height="9" fill="none" stroke="#bbb"/><line x1="0" y1="4" x2="11" y2="4" stroke="#bbb"/></svg>dd/mm/yyyy</div></div>
  <div class="field" style="left:728px;width:120px"><label>RETURNING</label><div class="box"><svg width="11" height="11" viewBox="0 0 11 11"><rect x=".5" y="1.5" width="10" height="9" fill="none" stroke="#bbb"/><line x1="0" y1="4" x2="11" y2="4" stroke="#bbb"/></svg>dd/mm/yyyy</div></div>
  <div class="field" style="left:853px;width:51px"><label>ROOMS</label><div class="box select">1<svg width="10" height="6"><path d="M1 1l4 4 4-4" fill="none" stroke="#333" stroke-width="1.5"/></svg></div></div>
  <div class="field" style="left:909px;width:67px"><label>ADULTS (18+)</label><div class="box select">2<svg width="10" height="6"><path d="M1 1l4 4 4-4" fill="none" stroke="#333" stroke-width="1.5"/></svg></div></div>
  <div class="field" style="left:981px;width:77px"><label>CHILDREN (0-17)</label><div class="box select">0<svg width="10" height="6"><path d="M1 1l4 4 4-4" fill="none" stroke="#333" stroke-width="1.5"/></svg></div></div>
  <div class="abs addcar"><i></i>Add a Car</div>
  <div class="btn">Search</div>
</section>

<h2 class="abs heading fav-title">SELECT YOUR FAVOURITES</h2>
<div class="abs fav-tabs">
  <span class="active" style="left:248px">Top Deals</span>
  <span style="left:374px">Featured Destinations</span>
  <span style="left:556px">Popular Packages</span>
</div>

<div class="card" style="left:142px;background:linear-gradient(160deg,#8aa3b8,#5b6c7e 55%,#3a4350)" role="img" aria-label="New York skyscrapers seen from below">
  <span class="label">Newyork Deals</span>
  <svg class="corner" width="36" height="36" viewBox="0 0 36 36"><path d="M36 0V36H0z" fill="var(--gold)"/><path d="M25 16l1.6 3.6 3.9.3-3 2.6.9 3.8-3.4-2-3.4 2 .9-3.8-3-2.6 3.9-.3z" fill="var(--ink)"/></svg>
</div>
<div class="card" style="left:373px;background:linear-gradient(170deg,#7f6aa8,#c77e6e 40%,#4a3f6a 75%,#2f2a4a)" role="img" aria-label="Las Vegas welcome sign at sunset">
  <span class="label">Las Vegas Deals</span>
  <svg class="corner" width="36" height="36" viewBox="0 0 36 36"><path d="M36 0V36H0z" fill="var(--gold)"/><path d="M25 16l1.6 3.6 3.9.3-3 2.6.9 3.8-3.4-2-3.4 2 .9-3.8-3-2.6 3.9-.3z" fill="var(--ink)"/></svg>
</div>
<div class="card" style="left:604px;background:linear-gradient(180deg,#2f8a86,#1d7a74 50%,#135e59)" role="img" aria-label="Misty green mountains by the sea">
  <div class="center"><div class="t">Bangkok Deals</div><div class="p">From <b>$500</b> per person</div></div>
  <svg class="corner" width="36" height="36" viewBox="0 0 36 36"><path d="M36 0V36H0z" fill="var(--gold)"/><path d="M25 16l1.6 3.6 3.9.3-3 2.6.9 3.8-3.4-2-3.4 2 .9-3.8-3-2.6 3.9-.3z" fill="var(--ink)"/></svg>
</div>
<div class="card" style="left:835px;background:linear-gradient(180deg,#7fb3d8,#6e9a7c 45%,#c9b79a 80%,#9a8a70)" role="img" aria-label="Tropical beach with a dancer and green cliffs">
  <span class="label">Hawaii Deals</span>
  <svg class="corner" width="36" height="36" viewBox="0 0 36 36"><path d="M36 0V36H0z" fill="var(--gold)"/><path d="M25 16l1.6 3.6 3.9.3-3 2.6.9 3.8-3.4-2-3.4 2 .9-3.8-3-2.6 3.9-.3z" fill="var(--ink)"/></svg>
</div>
<div class="abs fav-dots"><i class="on"></i><i></i><i></i><i></i></div>

<section class="abs forum">
  <div class="btn">View All</div>
</section>
<h2 class="abs heading forum-title">LATEST TRAVEL FORUM</h2>
<p class="abs forum-sub">Please share your experience here</p>
<table class="abs forum-table">
  <thead><tr><th class="c1">TITLE</th><th>POSTED ON</th><th class="c3">VIEWS / REPLIES</th></tr></thead>
  <tbody>
    <tr><td class="c1"><div class="topic">Why Hawaii is a hub for entertainment?</div>By : Dorin Vaskel</td><td>15 Jan 2017, 07:45 AM</td><td class="c3 stat">View : <b>1450</b><br>Replies : <b>45</b></td></tr>
    <tr><td class="c1"><div class="topic">Whis the hottest place in January?</div>By : Perin Aldovar</td><td>15 Jan 2017, 06:45 AM</td><td class="c3 stat">View : <b>1950</b><br>Replies : <b>75</b></td></tr>
    <tr><td class="c1"><div class="topic">Must visit destinations in the world which make you feel better...</div>By : Perin Aldovar</td><td>15 Jan 2017, 06:45 AM</td><td class="c3 stat">View : <b>1950</b><br>Replies : <b>75</b></td></tr>
    <tr><td class="c1"><div class="topic">Why Hawaii is a hub for entertainment?</div>By : Dorin Vaskel</td><td>15 Jan 2017, 07:45 AM</td><td class="c3 stat">View : <b>1450</b><br>Replies : <b>45</b></td></tr>
    <tr><td class="c1"><div class="topic">Whis the hottest place in January?</div>By : Perin Aldovar</td><td>15 Jan 2017, 06:45 AM</td><td class="c3 stat">View : <b>1950</b><br>Replies : <b>75</b></td></tr>
  </tbody>
</table>

<section class="abs newsletter" role="img" aria-label="Teal-toned lake with a moored boat">
  <div class="abs nl-title">SIGN UP TO OUR NEWSLETTER</div>
  <div class="abs nl-sub">Get updated for special offers</div>
  <div class="abs nl-input"><svg width="12" height="9" viewBox="0 0 12 9"><rect width="12" height="9" fill="#aaa"/><path d="M0 0l6 5 6-5" fill="none" stroke="#fff"/></svg>Enter your email address</div>
  <div class="abs btn nl-submit">Submit</div>
</section>

<h2 class="abs heading links-title">POPULAR LINKS YOU MAY INTERESTED</h2>

<div class="popular-links">
  <a class="plink" style="left:142px;top:1953px"><svg class="shape" width="289" height="51"><path d="M.5 .5H270L288.5 25.5 270 50.5H.5z" fill="#fff" stroke="var(--line)"/></svg><svg class="tick" width="13" height="11"><path d="M1 6l4 4 7-9" fill="none" stroke="var(--gold)" stroke-width="2"/></svg><span>New York Holidays</span></a>
  <a class="plink" style="left:455px;top:1953px"><svg class="shape" width="289" height="51"><path d="M.5 .5H270L288.5 25.5 270 50.5H.5z" fill="#fff" stroke="var(--line)"/></svg><svg class="tick" width="13" height="11"><path d="M1 6l4 4 7-9" fill="none" stroke="var(--gold)" stroke-width="2"/></svg><span>Amsterdam Hotels</span></a>
  <a class="plink" style="left:767px;top:1953px"><svg class="shape" width="289" height="51"><path d="M.5 .5H270L288.5 25.5 270 50.5H.5z" fill="#fff" stroke="var(--line)"/></svg><svg class="tick" width="13" height="11"><path d="M1 6l4 4 7-9" fill="none" stroke="var(--gold)" stroke-width="2"/></svg><span>Dubai Holidays</span></a>

  <a class="plink" style="left:142px;top:2013px"><svg class="shape" width="289" height="51"><path d="M.5 .5H270L288.5 25.5 270 50.5H.5z" fill="#fff" stroke="var(--line)"/></svg><svg class="tick" width="13" height="11"><path d="M1 6l4 4 7-9" fill="none" stroke="var(--gold)" stroke-width="2"/></svg><span>UK Car Hire</span></a>
  <a class="plink" style="left:455px;top:2013px"><svg class="shape" width="289" height="51"><path d="M.5 .5H270L288.5 25.5 270 50.5H.5z" fill="#fff" stroke="var(--line)"/></svg><svg class="tick" width="13" height="11"><path d="M1 6l4 4 7-9" fill="none" stroke="var(--gold)" stroke-width="2"/></svg><span>Oralando Flights</span></a>
  <a class="plink" style="left:767px;top:2013px"><svg class="shape" width="289" height="51"><path d="M.5 .5H270L288.5 25.5 270 50.5H.5z" fill="#fff" stroke="var(--line)"/></svg><svg class="tick" width="13" height="11"><path d="M1 6l4 4 7-9" fill="none" stroke="var(--gold)" stroke-width="2"/></svg><span>Bangkok Flights</span></a>

  <a class="plink" style="left:142px;top:2073px"><svg class="shape" width="289" height="51"><path d="M.5 .5H270L288.5 25.5 270 50.5H.5z" fill="#fff" stroke="var(--line)"/></svg><svg class="tick" width="13" height="11"><path d="M1 6l4 4 7-9" fill="none" stroke="var(--gold)" stroke-width="2"/></svg><span>Sydney Flights</span></a>
  <a class="plink" style="left:455px;top:2073px"><svg class="shape" width="289" height="51"><path d="M.5 .5H270L288.5 25.5 270 50.5H.5z" fill="#fff" stroke="var(--line)"/></svg><svg class="tick" width="13" height="11"><path d="M1 6l4 4 7-9" fill="none" stroke="var(--gold)" stroke-width="2"/></svg><span>Hawaii Hotels</span></a>
  <a class="plink" style="left:767px;top:2073px"><svg class="shape" width="289" height="51"><path d="M.5 .5H270L288.5 25.5 270 50.5H.5z" fill="#fff" stroke="var(--line)"/></svg><svg class="tick" width="13" height="11"><path d="M1 6l4 4 7-9" fill="none" stroke="var(--gold)" stroke-width="2"/></svg><span>Paris Car Hire</span></a>

  <a class="plink" style="left:142px;top:2133px"><svg class="shape" width="289" height="51"><path d="M.5 .5H270L288.5 25.5 270 50.5H.5z" fill="#fff" stroke="var(--line)"/></svg><svg class="tick" width="13" height="11"><path d="M1 6l4 4 7-9" fill="none" stroke="var(--gold)" stroke-width="2"/></svg><span>New York Holidays</span></a>
  <a class="plink" style="left:455px;top:2133px"><svg class="shape" width="289" height="51"><path d="M.5 .5H270L288.5 25.5 270 50.5H.5z" fill="#fff" stroke="var(--line)"/></svg><svg class="tick" width="13" height="11"><path d="M1 6l4 4 7-9" fill="none" stroke="var(--gold)" stroke-width="2"/></svg><span>Amsterdam Hotels</span></a>
  <a class="plink" style="left:767px;top:2133px"><svg class="shape" width="289" height="51"><path d="M.5 .5H270L288.5 25.5 270 50.5H.5z" fill="#fff" stroke="var(--line)"/></svg><svg class="tick" width="13" height="11"><path d="M1 6l4 4 7-9" fill="none" stroke="var(--gold)" stroke-width="2"/></svg><span>Dubai Holidays</span></a>

  <a class="plink" style="left:142px;top:2193px"><svg class="shape" width="289" height="51"><path d="M.5 .5H270L288.5 25.5 270 50.5H.5z" fill="#fff" stroke="var(--line)"/></svg><svg class="tick" width="13" height="11"><path d="M1 6l4 4 7-9" fill="none" stroke="var(--gold)" stroke-width="2"/></svg><span>UK Car Hire</span></a>
  <a class="plink" style="left:455px;top:2193px"><svg class="shape" width="289" height="51"><path d="M.5 .5H270L288.5 25.5 270 50.5H.5z" fill="#fff" stroke="var(--line)"/></svg><svg class="tick" width="13" height="11"><path d="M1 6l4 4 7-9" fill="none" stroke="var(--gold)" stroke-width="2"/></svg><span>Oralando Flights</span></a>
  <a class="plink" style="left:767px;top:2193px"><svg class="shape" width="289" height="51"><path d="M.5 .5H270L288.5 25.5 270 50.5H.5z" fill="#fff" stroke="var(--line)"/></svg><svg class="tick" width="13" height="11"><path d="M1 6l4 4 7-9" fill="none" stroke="var(--gold)" stroke-width="2"/></svg><span>Bangkok Flights</span></a>
</div>

<footer>
  <div class="abs foot-brand">Rovanix</div>
  <nav class="abs foot-nav"><a>HOME</a><a>ABOUT US</a><a>CUSTOMER SUPPORT</a><a>PRIVACY</a><a>TERMS OF USE</a></nav>
  <div class="abs copy">© 2016 ROVANIX. ALL RIGHTS RESERVED.</div>
  <div class="abs skyline" role="img" aria-label="Golden city skyline with a plane taking off"></div>
</footer>

</body>
</html>
```